A start-up named "lumerova" - a clinical research organization needs a new PowerPoint design

We need a new PowerPoint Design (incl. business card and stationery design) for an early-stage start-up named "lumerova" seeking to build an ecosystem/ strategic partner alliances or consortium of committed and active collaborators to guide important components of the clinical trial.

Our ultimate goal is to avoid false neutrals – therapies that have not been and may never be evaluated in clinical trials due to the costs and/ or complexity.

The final design should highlight our patient-centric approach, innovative study design supported with the novel AI platform to make a stronger impact on patient lives.

Please see the attached brief for more details.
Updates

Requesting the proposals on color-coding, business-card designs, clinical research visuals, and icons as well as stationery design.

Target Market(s)

Pharma/ Biotech Executives
Medical Institutions
Clinical Trial Participants (Patients)

Colors
e34398

Requirements
Must have
• Use the Color Version of purple/ magenta logo

```html
<!DOCTYPE html>
<html lang="en">
<head>
<meta charset="utf-8">
<title>lumerova — stationery</title>
<link rel="stylesheet" href="https://fonts.googleapis.com/css2?family=Ubuntu:wght@300;400;500;700&display=swap">
<style>
  :root {
    --magenta: #b02a74;
    --magenta-deep: #9c2163;
    --magenta-flap: #a8266c;
    --pink-band: #f0a6d2;
    --pink-rule: #f3a9d4;
    --white: #ffffff;
    --card-edge: #2b2440;
    --backdrop: #e8e6e7;
  }
  * { box-sizing: border-box; margin: 0; padding: 0; }
  html, body { width: 1200px; height: 900px; overflow: hidden; }
  body {
    background: var(--backdrop);
    font-family: "Ubuntu", sans-serif;
    color: var(--white);
    position: relative;
  }
  .sheet { position: absolute; background: var(--magenta); overflow: hidden; }

  .wordmark {
    font-family: "Ubuntu", sans-serif;
    font-weight: 500;
    color: var(--white);
    display: inline-flex;
    align-items: flex-start;
    gap: 0.18em;
    letter-spacing: -0.01em;
    line-height: 1;
  }
  .wordmark .dot {
    width: 0.34em; height: 0.34em;
    background: var(--white);
    margin-top: -0.05em;
  }
  b { font-weight: 700; }

  /* Business card — front */
  .card-front {
    left: 60px; top: 150px; width: 230px; height: 150px;
    border-right: 3px solid var(--card-edge);
    border-bottom: 2px solid var(--card-edge);
  }
  .card-front .name { position: absolute; left: 28px; top: 30px; font-size: 17px; font-weight: 500; }
  .card-front .position { position: absolute; left: 28px; top: 51px; font-size: 14px; font-weight: 300; }
  .card-front .contacts { position: absolute; left: 28px; top: 94px; list-style: none; font-size: 7px; }
  .card-front .contacts li { display: flex; align-items: center; gap: 6px; height: 11px; }
  .card-front .contacts svg { width: 8px; height: 8px; }
  .card-front .side-band {
    position: absolute; right: 0; top: 0; width: 24px; height: 100%;
    background: var(--pink-band);
    border-left: 2px solid var(--magenta-deep);
  }
  .card-front .side-band span {
    position: absolute; left: 50%; top: 50%;
    transform: translate(-50%, -50%) rotate(-90deg);
    white-space: nowrap; font-size: 6.5px; line-height: 1.1;
    color: var(--magenta); text-align: center;
  }

  /* Business card — back */
  .card-back {
    left: 60px; top: 330px; width: 230px; height: 150px;
    border-right: 3px solid var(--card-edge);
    border-bottom: 2px solid var(--card-edge);
    display: flex; align-items: center; justify-content: center;
  }
  .card-back .wordmark { font-size: 22px; }

  /* Letterhead */
  .letterhead { left: 320px; top: 120px; width: 430px; height: 608px; }
  .letterhead .wordmark { position: absolute; right: 44px; top: 46px; font-size: 19px; }
  .letterhead .headline {
    position: absolute; left: 42px; top: 130px;
    font-size: 26px; font-weight: 700; line-height: 1.02; text-transform: uppercase;
  }
  .headline .rule {
    display: inline-block; width: 64px; height: 5px; background: var(--pink-rule);
    vertical-align: middle; margin-left: 12px;
  }
  .letterhead .lead {
    position: absolute; left: 42px; top: 252px; width: 350px;
    font-size: 12.5px; font-weight: 300; line-height: 1.5;
  }
  .letterhead .body { position: absolute; left: 42px; top: 345px; width: 345px; }
  .letterhead .body p { font-size: 8.5px; font-weight: 300; line-height: 1.5; margin-bottom: 10px; }
  .letterhead .care-icon {
    position: absolute; left: 42px; top: 520px; width: 60px; height: 60px;
    background: var(--pink-band); border-radius: 6px; opacity: 0.85;
  }

  /* Envelope */
  .envelope { left: 790px; top: 120px; width: 360px; height: 255px; background: var(--magenta); }
  .envelope svg.flap { position: absolute; inset: 0; width: 100%; height: 100%; }
  .envelope .wordmark { position: absolute; left: 130px; top: 48px; font-size: 19px; }
  .envelope .note {
    position: absolute; left: 40px; right: 40px; bottom: 20px;
    font-size: 4.6px; font-weight: 300; line-height: 1.5; text-align: center;
  }

  /* Compliment slip */
  .slip { left: 790px; top: 430px; width: 360px; height: 172px; }
  .slip .band { position: absolute; left: 0; top: 0; width: 28px; height: 100%; background: var(--pink-band); }
  .slip .wordmark { position: absolute; right: 26px; top: 20px; font-size: 15px; }
  .slip .headline {
    position: absolute; left: 66px; top: 46px;
    font-size: 12.5px; font-weight: 700; line-height: 1.05; text-transform: uppercase;
  }
  .slip .headline .rule { width: 62px; height: 2.5px; margin-left: 8px; }
  .slip .lead {
    position: absolute; left: 66px; top: 80px; width: 270px;
    font-size: 6.3px; font-weight: 300; line-height: 1.45;
  }
  .slip .body { position: absolute; left: 66px; top: 114px; width: 276px; }
  .slip .body p { font-size: 3.8px; font-weight: 300; line-height: 1.45; margin-bottom: 4px; }
</style>
</head>
<body>

  <section class="sheet card-front" aria-label="Business card, front">
    <p class="name">Your name</p>
    <p class="position">position</p>
    <ul class="contacts">
      <li>
        <svg viewBox="0 0 10 10" aria-hidden="true"><circle cx="5" cy="5" r="5" fill="#f0a6d2"/><path d="M3.3 2.6l1 1-.6.7a4 4 0 0 0 2 2l.7-.6 1 1-.7.8C5 7.3 2.7 5 2.5 3.3z" fill="#b02a74"/></svg>
        <span>123456789</span>
      </li>
      <li>
        <svg viewBox="0 0 10 10" aria-hidden="true"><circle cx="5" cy="5" r="5" fill="#f0a6d2"/><rect x="2.6" y="3.3" width="4.8" height="3.4" fill="none" stroke="#b02a74" stroke-width=".7"/><path d="M2.6 3.3L5 5.2l2.4-1.9" fill="none" stroke="#b02a74" stroke-width=".7"/></svg>
        <span>123456789@lumerova.example</span>
      </li>
      <li>
        <svg viewBox="0 0 10 10" aria-hidden="true"><circle cx="5" cy="5" r="5" fill="#f0a6d2"/><path d="M5 2.3a1.9 1.9 0 0 1 1.9 1.9C6.9 5.6 5 7.7 5 7.7S3.1 5.6 3.1 4.2A1.9 1.9 0 0 1 5 2.3z" fill="#b02a74"/></svg>
        <span>Your address</span>
      </li>
    </ul>
    <div class="side-band"><span>WE STRIVE TO WORK LUMEROVA<br>(FOR SAPIENS)</span></div>
  </section>

  <section class="sheet card-back" aria-label="Business card, back">
    <span class="wordmark">lumerova<i class="dot"></i></span>
  </section>

  <section class="sheet letterhead" aria-label="Letterhead">
    <span class="wordmark">lumerova<i class="dot"></i></span>
    <h1 class="headline">We strive to<span class="rule"></span><br>work lumerova<br>(for sapiens)</h1>
    <p class="lead">LUMEROVA is an early-stage start-up seeking to <b>build an ecosystem/strategic partner alliances</b> or consortium of committed and active collaborators to guide important components of the clinical trial</p>
    <div class="body">
      <p>The Science around new medical treatments is rapidly progressing, but there are many questions surrounding <b>how Science could Translate into a Therapy</b></p>
      <p>Success lies in moving from an idea generating phase at a 50.000-foot level to the on-the ground implementation phase. It is crucial to strike a balance between what is <b>scientifically valuable and operationally feasible</b></p>
      <p>We have no time or money to spend on wasted efforts. We really need to focus on tasks where we/ patients could gain something. We have to figure out how we can best use science at our disposal to avoid type 1 error but also <b>get superior treatments to patients</b></p>
    </div>
    <div class="care-icon" role="img" aria-label="Icon of two open hands holding a heart"></div>
  </section>

  <section class="sheet envelope" aria-label="Envelope">
    <svg class="flap" viewBox="0 0 360 255" preserveAspectRatio="none" aria-hidden="true">
      <path d="M0 255 L150 120 M360 255 L210 120" stroke="#9c2163" stroke-width="1" fill="none" opacity=".6"/>
      <path d="M0 0 H360 L194 176 Q180 190 166 176 Z" fill="#a8266c"/>
      <path d="M8 6 L180 180" stroke="#8f1d5a" stroke-width="1" opacity=".35"/>
    </svg>
    <span class="wordmark">lumerova<i class="dot"></i></span>
    <p class="note">LUMEROVA is an early-stage start-up seeking to <b>build an ecosystem/ strategic partner alliances</b> or consortium<br>of committed and active collaborators to guide important components of the clinical trial</p>
  </section>

  <section class="sheet slip" aria-label="Compliment slip">
    <div class="band"></div>
    <span class="wordmark">lumerova<i class="dot"></i></span>
    <h2 class="headline">We strive to work<span class="rule"></span><br>lumerova (for sapiens)</h2>
    <p class="lead">LUMEROVA is an early-stage start-up seeking to <b>build an ecosystem/strategic partner alliances</b> or consortium of committed and active collaborators to guide important components of the clinical trial</p>
    <div class="body">
      <p>The Science around new medical treatments is rapidly progressing, but there are many questions surrounding <b>how Science could Translate into a Therapy</b></p>
      <p>Success lies in moving from an idea generating phase at a 50.000-foot level to the on-the ground implementation phase. It is crucial to strike a balance between what is <b>scientifically valuable and operationally feasible</b></p>
      <p>We have no time or money to spend on wasted efforts. We really need to focus on tasks where we/ patients could gain something. We have to figure out how we can best use science at our disposal to avoid type 1 error but also <b>get superior treatments to patients</b></p>
    </div>
  </section>

</body>
</html>
```